Business Card Design For A Renovation Contractor Company

We need a business card for a new company based in Singapore, our company name is "RB Tolvane". We are a renovation contractor that builds designs into reality. We build more of F&B restaurants, retail stores and commercial offices. We work very closely with designers. The final design should communicate to our client that we are a company that you can trust, that will plan and complete your project without giving you a headache. I like my client to remember my company as "RB". The beauty of SIMPLE is important.

Industry/Entity Type

Contractor

Requirements
Nice to have
• Black or Red base

```html
<!DOCTYPE html>
<html lang="en">
<head>
<meta charset="utf-8">
<title>RB Tolvane – Business Card</title>
<link rel="stylesheet" href="https://fonts.googleapis.com/css2?family=Didact+Gothic&family=Source+Sans+3:wght@400;600;700&display=swap">
<style>
  :root {
    --backdrop: #e9e6e2;
    --card: #ffffff;
    --ink: #1a1a1a;
    --ink-soft: #3a3a3a;
    --red: #e3242b;
    --rule: #cfcfcf;
    --card-w: 520px;
    --card-h: 297px;
  }
  * { margin: 0; padding: 0; box-sizing: border-box; }
  html, body {
    width: 1200px;
    height: 720px;
    overflow: hidden;
    background: var(--backdrop);
  }
  .stage {
    width: 1200px;
    height: 720px;
    display: flex;
    align-items: center;
    justify-content: center;
    gap: 60px;
  }
  .card {
    position: relative;
    width: var(--card-w);
    height: var(--card-h);
    background: var(--card);
    box-shadow: 0 2px 8px rgba(0,0,0,0.12);
    overflow: hidden;
  }

  /* Brand block */
  .brand { display: flex; flex-direction: column; align-items: center; }
  .brand-mark {
    border-radius: 50%;
    background: var(--red);
  }
  .brand-name {
    font-family: "Didact Gothic", sans-serif;
    font-weight: 400;
    color: var(--ink);
    letter-spacing: 0.5px;
    line-height: 1;
    white-space: nowrap;
  }
  .brand-tagline {
    font-family: "Didact Gothic", sans-serif;
    color: var(--ink-soft);
    border-top: 1px solid var(--ink-soft);
    letter-spacing: 0.6px;
    line-height: 1;
    white-space: nowrap;
  }

  /* Contact side */
  .card-contact .brand {
    position: absolute;
    left: 22px; top: 62px;
    width: 210px;
  }
  .card-contact .brand-mark { width: 50px; height: 50px; margin-bottom: 12px; }
  .card-contact .brand-name { font-size: 31px; }
  .card-contact .brand-tagline { font-size: 11.5px; margin-top: 3px; padding: 3px 4px 0; }

  .divider {
    position: absolute;
    left: 255px; top: 26px;
    width: 1px; height: 190px;
    background: var(--rule);
  }
  .person {
    position: absolute;
    left: 272px; top: 24px;
    font-family: "Source Sans 3", sans-serif;
    color: var(--ink);
  }
  .person-name { font-size: 17px; font-weight: 700; line-height: 1.1; }
  .person-title { font-size: 12px; font-weight: 600; color: var(--red); margin-bottom: 6px; }
  .contact-list { list-style: none; font-size: 12.5px; line-height: 1.35; }
  .contact-list li { display: flex; align-items: center; gap: 6px; }
  .contact-list svg { width: 11px; height: 11px; flex: none; }
  .contact-list .address { align-items: flex-start; margin-top: 6px; }
  .contact-list .address svg { margin-top: 3px; }

  .footer-bands {
    position: absolute;
    left: 0; bottom: 0;
    width: 100%; height: 40px;
  }

  /* Front side */
  .card-front .brand {
    position: absolute;
    left: 50%; top: 58px;
    transform: translateX(-50%);
  }
  .card-front .brand-mark { width: 58px; height: 58px; margin-bottom: 14px; }
  .card-front .brand-name { font-size: 42px; }
  .card-front .brand-tagline { font-size: 15px; margin-top: 4px; padding: 4px 6px 0; }
  .web-address {
    position: absolute;
    left: 0; right: 0; bottom: 44px;
    text-align: center;
    font-family: "Source Sans 3", sans-serif;
    font-size: 15px;
    letter-spacing: 3px;
    color: var(--ink-soft);
  }
  .web-address .accent { color: var(--red); }
</style>
</head>
<body>
<main class="stage">

  <section class="card card-contact" aria-label="Business card, contact side">
    <div class="brand">
      <span class="brand-mark"></span>
      <span class="brand-name">RB Tolvane</span>
      <span class="brand-tagline">crafted spaces, done right</span>
    </div>

    <span class="divider"></span>

    <div class="person">
      <p class="person-name">Your Name</p>
      <p class="person-title">Title</p>
      <ul class="contact-list">
        <li>
          <svg viewBox="0 0 12 12"><circle cx="6" cy="6" r="6" fill="var(--red)"/><path d="M3.6 3.2l1.2-.4.7 1.6-.7.5c.4.9 1 1.5 1.9 1.9l.5-.7 1.6.7-.4 1.2c-2.5 0-4.8-2.3-4.8-4.8z" fill="#fff"/></svg>
          123-456-0789
        </li>
        <li>
          <svg viewBox="0 0 12 12"><circle cx="6" cy="6" r="6" fill="var(--red)"/><rect x="4.2" y="2.6" width="3.6" height="6.8" rx="0.6" fill="#fff"/><rect x="4.8" y="3.4" width="2.4" height="4.2" fill="var(--red)"/></svg>
          123-456-0789
        </li>
        <li>
          <svg viewBox="0 0 12 12"><circle cx="6" cy="6" r="6" fill="var(--red)"/><rect x="3" y="4" width="6" height="4.2" fill="#fff"/><path d="M3 4l3 2.3L9 4" fill="none" stroke="var(--red)" stroke-width="0.7"/></svg>
          info@rbtolvane.com
        </li>
        <li>
          <svg viewBox="0 0 12 12"><circle cx="6" cy="6" r="6" fill="var(--red)"/><circle cx="6" cy="6" r="3.2" fill="none" stroke="#fff" stroke-width="0.8"/><path d="M2.8 6h6.4M6 2.8c-1.5 1.8-1.5 4.6 0 6.4M6 2.8c1.5 1.8 1.5 4.6 0 6.4" fill="none" stroke="#fff" stroke-width="0.6"/></svg>
          www.rbtolvane.com
        </li>
        <li class="address">
          <svg viewBox="0 0 12 12"><circle cx="6" cy="6" r="6" fill="var(--red)"/><path d="M6 2.5a2.3 2.3 0 0 1 2.3 2.3C8.3 6.6 6 9.4 6 9.4S3.7 6.6 3.7 4.8A2.3 2.3 0 0 1 6 2.5z" fill="#fff"/><circle cx="6" cy="4.8" r="0.8" fill="var(--red)"/></svg>
          <span>Street Name, City Name<br>State Zip Code</span>
        </li>
      </ul>
    </div>

    <svg class="footer-bands" viewBox="0 0 520 40" preserveAspectRatio="none" aria-hidden="true">
      <polygon points="0,26 262,26 250,40 0,40" fill="var(--ink)"/>
      <polygon points="262,26 520,10 520,22 275,40 250,40" fill="var(--red)"/>
      <polygon points="275,40 520,22 520,40" fill="var(--card)"/>
      <rect x="0" y="36" width="250" height="4" fill="var(--card)"/>
    </svg>
  </section>

  <section class="card card-front" aria-label="Business card, front side">
    <div class="brand">
      <span class="brand-mark"></span>
      <span class="brand-name">RB Tolvane</span>
      <span class="brand-tagline">crafted spaces, done right</span>
    </div>
    <p class="web-address">www.rb<span class="accent">tolvane</span>.com</p>
  </section>

</main>
</body>
</html>
```